Penny Harvest

Logo and general packaging design for premium quality, price conscious super foods.

Initial product portfolio includes:

Organic Raw Chia Seeds - Resealable plastic bags with 3 x 5 label.
Organic Cold Pressed Coconut Oil (plastic jar) - 2.5 x 6.5 label

The design should be transferable to additional products.

Project requirements:

The design should be simple and the core trade dress should be no more than 2 or 3 colors. The logo should reproduce well in black/1 color.

The idea of this design is to convey quality and simplicity, like a "no frills", premium quality brand.

Deliverable: fully editable (text and illustration):

Logo.

Basic Jar label design.

Basic Bag label design.

Target Market(s)

Educated women aged 22-45

Industry/Entity Type

Plastic

Requirements
Must have
• Clear, simple logo, delivered in vector form, 1 color/black.
• Use of logo on 1 jar label and 1 bag label, each with product name and space for required and optional marketing content.
Nice to have
• Additional iterations of the design to demonstrate your concept of how we will visually vary additional items in jars and bags.
• i.e. What an additional product in a bag would look like for purposes of brand consistency and product differentiation on shelf or online in e-store.
Should not have
• overly detailed graphics that don't scale well and/or may be hard to read or understand. 4 color design elements (except to simiulate how the product may look through the clear jar or bag or how the product may be placed in a simulated surrounding or ad.

```html
<!DOCTYPE html>
<html lang="en">
<head>
<meta charset="utf-8">
<title>Penny Harvest – Organic Raw Chia Seeds Label</title>
<link rel="stylesheet" href="https://fonts.googleapis.com/css2?family=Alfa+Slab+One&family=Arimo:wght@400;700&display=swap">
<style>
  :root {
    --forest: #0f4a22;
    --olive: #6a7b35;
    --cream: #ffffff;
    --sprig-light: #8fa77f;
  }
  html, body {
    margin: 0;
    padding: 0;
    overflow: hidden;
    background: #ffffff;
  }
  .label {
    position: relative;
    width: 1200px;
    height: 721px;
    background: var(--olive);
    overflow: hidden;
    font-family: "Arimo", Arial, sans-serif;
    color: var(--cream);
  }
  .side-panel {
    position: absolute;
    left: 0;
    top: 0;
    width: 399px;
    height: 721px;
    background: var(--forest);
  }
  .plant-art {
    position: absolute;
    left: 64px;
    top: 48px;
    width: 303px;
    height: 673px;
    background: linear-gradient(180deg, rgba(255,255,255,0.10) 0%, rgba(255,255,255,0.28) 45%, rgba(255,255,255,0.16) 100%);
    border-radius: 40px 40px 0 0;
  }
  .natural-seal {
    position: absolute;
    left: 35px;
    top: 550px;
    width: 122px;
    height: 122px;
    border-radius: 50%;
    background: var(--olive);
    display: flex;
    flex-direction: column;
    align-items: center;
    justify-content: center;
    font-weight: 700;
    line-height: 1;
  }
  .natural-seal .pct { font-size: 27px; }
  .natural-seal .word { font-size: 25px; margin-top: 2px; }
  .brand-name {
    position: absolute;
    left: 440px;
    width: 760px;
    top: 70px;
    text-align: center;
    font-family: "Arimo", Arial, sans-serif;
    font-weight: 700;
    font-size: 38px;
    letter-spacing: 2px;
    color: var(--cream);
  }
  .product-title {
    position: absolute;
    left: 440px;
    width: 760px;
    top: 188px;
    margin: 0;
    text-align: center;
    font-family: "Alfa Slab One", Georgia, serif;
    font-weight: 400;
    line-height: 1;
  }
  .product-title .line-main {
    display: block;
    font-size: 112px;
    letter-spacing: 4px;
  }
  .product-title .line-sub {
    display: block;
    font-size: 55px;
    letter-spacing: 2px;
    margin-top: 14px;
  }
  .divider {
    position: absolute;
    left: 730px;
    top: 380px;
    width: 180px;
    height: 2px;
    background: var(--cream);
  }
  .benefits {
    position: absolute;
    left: 440px;
    width: 760px;
    top: 397px;
    text-align: center;
    font-weight: 700;
    font-size: 21px;
    letter-spacing: 0.5px;
  }
  .net-weight {
    position: absolute;
    left: 440px;
    width: 760px;
    top: 490px;
    text-align: center;
    font-weight: 700;
    font-size: 17px;
  }
  .marketer, .dates {
    position: absolute;
    top: 648px;
    font-weight: 700;
    font-size: 16px;
    line-height: 1.5;
  }
  .marketer { left: 460px; }
  .dates { left: 768px; }
</style>
</head>
<body>
  <main class="label">
    <div class="side-panel">
      <div class="plant-art" role="img" aria-label="White illustration of flowering chia plant stems"></div>
      <div class="natural-seal">
        <span class="pct">100%</span>
        <span class="word">natural</span>
      </div>
    </div>

    <div class="brand-name">PENNY HARVEST</div>

    <h1 class="product-title">
      <span class="line-main">ORGANIC</span>
      <span class="line-sub">RAW CHIA SEEDS</span>
    </h1>

    <div class="divider"></div>

    <p class="benefits" style="margin:0">ANTIOXIDANTS | CALCIUM | OMEGA FATTY ACIDS</p>

    <p class="net-weight" style="margin:0">Net Weight 100gms</p>

    <p class="marketer" style="margin:0">Marketed by: Penny Harvest<br>Lane 12, Millbrook, 40217</p>

    <p class="dates" style="margin:0">Date of packing:<br>Expiry date:</p>
  </main>
</body>
</html>
```